Business Card Design

I need a logo and a business card design that can be used for my business stationary, Facebook page and in the future a website. I don't know if I need a large design for brochures and stationery and a small portion of that as the logo or business card design. I probably need some advice about that. My new company is called Willowbank Family Circle. I don't have all of my business contact details available yet, but I want to get the design ready, so that when all this information is available I can get the printing done quickly.I'm a social worker and my business will be providing parenting groups and counselling sessions for parents.I would like the logo and business card to be very feminine and pretty. I want a silhouette image of a Mother and Baby and decorative swirls of flowers/vines/leaves and butterflies.I have found some designs elsewhere that are along the lines of what I am looking for. These images are attached below, but the quality of these attachments is very poor as I photographed them with my phone.My preferred colours would be to use black and white, purple and/or pink, aqua and or blue/green.There are four logo/business card options attached. Logo option 1 - I really like the flower and vine design. Logo option 2 - again I like the flowers and leaf design and the use of colour and the silhouette image of the Mum and Baby; Logo option 3 - I like the butterflies and decorative swirls in this option and Logo option 4 - I think this design is the best for a logo. I love the mother and baby image. I don't like the tree branch and the birds but I like the way the hair has been incorporated into the branch. I prefer the design of the flowers/vine/leaves in the other options.

Industry/Entity Type

Business

Contact Information for Business Card

Company Name:Embrace Attachment ParentingMobile:0417 751 394Email:Currently sourcing - TBAContact Name:Janelle ApplegarthQualifications:Currently sourcing details - TBA

Font styles to use
Script

Colors
33a6d7
85cae6
886aae
6c459b
e667a6
eea4c8

Requirements
Must have
• My project must have an image of a mother and child, slightly encircled by the mother's hair perhaps in a heart shape, and the mother's hair becoming a beautiful filigree design of vine/leaves/flowers and with some butterfly somewhere.
• Can all of the Words be in the same font Attachment Parenting can be slightly smaller.
Nice to have
• I would like to also have a similar vine/leaves/flowers and maybe a butterfly on the opposite side of the card. Maybe the Mother/child image on the top left of the card and the other pattern on the bottom right.
• If possible the use of aqua, purple and pink.

```html
<!DOCTYPE html>
<html lang="en">
<head>
<meta charset="utf-8">
<title>Willowbank Family Circle – Business Card</title>
<link rel="stylesheet" href="https://fonts.googleapis.com/css2?family=Open+Sans:wght@400;600&display=swap">
<style>
  :root {
    --teal: #13a0a6;
    --teal-deep: #0f7380;
    --charcoal: #3a3a3c;
    --ink: #3d3d3f;
    --paper: #ffffff;
  }
  html, body {
    margin: 0;
    padding: 0;
    width: 1200px;
    height: 686px;
    overflow: hidden;
    background: var(--paper);
  }
  .card {
    position: relative;
    width: 1200px;
    height: 686px;
    box-sizing: border-box;
    border: 1px solid var(--teal);
    background: var(--paper);
    font-family: "Open Sans", Arial, sans-serif;
    color: var(--ink);
    overflow: hidden;
  }
  .brand-mark {
    position: absolute;
    left: 272px;
    top: 66px;
    width: 140px;
    height: 140px;
    border-radius: 50%;
    background: var(--teal);
  }
  .brand-name {
    position: absolute;
    left: 0;
    top: 268px;
    width: 684px;
    margin: 0;
    text-align: center;
    font-weight: 600;
    font-size: 54px;
    line-height: 62px;
    color: var(--teal-deep);
  }
  .brand-rule {
    position: absolute;
    left: 0;
    top: 416px;
    width: 679px;
    height: 11px;
    background: var(--teal);
  }
  .contact {
    position: absolute;
    left: 34px;
    margin: 0;
    display: flex;
    align-items: center;
    font-size: 29px;
    color: var(--ink);
  }
  .contact svg { width: 50px; height: 40px; flex: none; }
  .contact span { margin-left: 51px; }
  .contact--email { top: 464px; }
  .contact--phone { top: 554px; }
  .person {
    position: absolute;
    left: 700px;
    top: 344px;
    width: 488px;
    text-align: center;
  }
  .person-name {
    margin: 0;
    font-weight: 400;
    font-size: 50px;
    line-height: 64px;
    color: var(--ink);
  }
  .person-role {
    margin: 0;
    font-size: 24px;
    line-height: 30px;
    color: var(--teal-deep);
  }
  .footer-bands {
    position: absolute;
    left: 0;
    bottom: 0;
    width: 1200px;
    height: 47px;
  }
</style>
</head>
<body>
<main class="card">
  <div class="brand-mark" aria-hidden="true"></div>
  <h1 class="brand-name">Willowbank<br>Family Circle</h1>
  <div class="brand-rule"></div>

  <p class="contact contact--email">
    <svg viewBox="0 0 50 40" aria-hidden="true">
      <rect x="1" y="4" width="48" height="32" fill="var(--teal)"/>
      <polyline points="1,4 25,24 49,4" fill="none" stroke="#fff" stroke-width="2.5"/>
      <line x1="1" y1="36" x2="19" y2="19" stroke="#fff" stroke-width="2"/>
      <line x1="49" y1="36" x2="31" y2="19" stroke="#fff" stroke-width="2"/>
    </svg>
    <span>Currently Sourcing</span>
  </p>

  <p class="contact contact--phone">
    <svg viewBox="0 0 50 44" aria-hidden="true">
      <path d="M10 3 L17 12 L13 18 Q18 28 28 32 L34 27 L43 34 L38 41 Q24 43 13 31 Q3 20 4 8 Z" fill="var(--teal)"/>
    </svg>
    <span>0438 260 517</span>
  </p>

  <div class="person">
    <h2 class="person-name">Rosalind Thackeray</h2>
    <p class="person-role">(DIRECTOR)</p>
  </div>

  <svg class="footer-bands" viewBox="0 0 1200 47" preserveAspectRatio="none" aria-hidden="true">
    <polygon points="0,0 893,0 867,47 0,47" fill="var(--teal-deep)"/>
    <polygon points="913,0 1200,0 1200,47 887,47" fill="var(--charcoal)"/>
  </svg>
</main>
</body>
</html>
```